ORV Web Design Project

I'm looking for a small, friendly,functional, information based website. If you go through the attachments, you would know the nature of the business.
Updates

Hi,

I have uploaded a picture of the CEO, Mr. Delvan Kroth PLMAT member. Please feel free to use it whereever appropriate.

Thanks!

Hello, I have uploaded some references. I like the colours used on the bar and would w

Example of a we page . I like this layout for the inside pages.

I am changing the tabs on my website to:

Home
About us
Services
Contact us

The services tab will have three sub pages:

Immigration
Education
AccommodationAccommodation

Target Market(s)

Young international students willing to come to Canada to study, young international students willing to immigrate to Canada, parents of the students

Industry/Entity Type

Business

Requirements
Must have
• ORV HOME
ABOUT US
CONTACT
SERVICES
TAG LINE

The website should look n feel trendy, smart, current, factual, trustworthy etc....
Nice to have
• I am looking for a bold, attractive, eye catchy home page with less text! Something that makes a statement....
Should not have
• No Clip art, flash animation, no bells n whistles please

```html
<!DOCTYPE html>
<html lang="en">
<head>
<meta charset="utf-8">
<title>ORV – About Us</title>
<link href="https://fonts.googleapis.com/css2?family=Montserrat:wght@500;800;900&family=Hind:wght@500;600&display=swap" rel="stylesheet">
<style>
  :root {
    --black: #000000;
    --white: #ffffff;
    --red: #ed1c24;
    --panel: #474747;
    --map-red: rgba(150, 18, 24, 0.6);
    --text-dark: #222222;
  }
  * { box-sizing: border-box; margin: 0; padding: 0; }
  html, body { width: 1200px; height: 701px; overflow: hidden; background: var(--white); }
  .page { position: relative; width: 1200px; height: 701px; font-family: "Hind", sans-serif; }

  .banner {
    position: absolute; left: 0; top: 0; width: 1200px; height: 103px;
    background: var(--black); color: var(--white);
    font-family: "Montserrat", sans-serif; font-weight: 900;
    font-size: 70px; letter-spacing: 3px; line-height: 103px; text-align: center;
  }

  .map-decor {
    position: absolute; left: 290px; top: 122px; width: 780px; height: 570px;
    background: radial-gradient(ellipse at 50% 50%, var(--map-red) 0%, rgba(150,18,24,0.35) 50%, rgba(150,18,24,0) 72%);
    z-index: 2;
  }

  .brand { position: absolute; left: 97px; top: 175px; }
  .brand-row { display: flex; align-items: center; gap: 10px; }
  .brand-name {
    font-family: "Montserrat", sans-serif; font-weight: 900; font-size: 64px;
    line-height: 1; color: var(--black);
  }
  .brand-dot { width: 30px; height: 30px; border-radius: 50%; background: var(--red); }
  .tagline { margin-top: 10px; font-style: italic; font-size: 12px; color: var(--text-dark); }

  .nav { position: absolute; left: 97px; top: 304px; width: 147px; list-style: none; }
  .nav li {
    height: 26px; margin-bottom: 5.5px; background: var(--black); color: var(--white);
    font-family: "Montserrat", sans-serif; font-weight: 800; font-size: 16px;
    line-height: 27px; padding-left: 2px; display: flex; align-items: center; gap: 4px;
  }
  .nav li.active { background: var(--red); }
  .nav svg { width: 14px; height: 14px; flex: none; }

  .member { position: absolute; left: 98px; top: 505px; display: flex; align-items: center; gap: 12px; }
  .member-badge { width: 82px; height: 82px; border-radius: 50%; background: #5a86c5; }
  .member-name { font-family: "Hind", sans-serif; font-weight: 600; font-size: 34px; color: #3e3e3e; }

  .social { position: absolute; left: 99px; top: 620px; display: flex; gap: 6px; }
  .social span { width: 26px; height: 26px; border-radius: 50%; background: var(--black); }
  .social span:first-child { background: var(--red); }

  .content { position: absolute; left: 298px; top: 150px; width: 805px; }
  .content-title {
    height: 55px; background: var(--red); color: var(--white);
    font-family: "Montserrat", sans-serif; font-weight: 500; font-size: 36px;
    line-height: 58px; padding-left: 31px; position: relative; z-index: 3;
  }
  .content-body {
    margin-top: 2px; height: 434px; background: var(--panel); position: relative;
    padding: 28px 30px 0 30px; color: var(--white);
    font-weight: 600; font-size: 13.3px; line-height: 20.3px;
  }
  .content-body p { position: relative; z-index: 3; margin-bottom: 20px; }
  .content-body p.narrow { width: 482px; }
  .highlight { color: var(--red); font-size: 18px; font-weight: 600; }

  .portrait {
    position: absolute; left: 534px; top: 152px; width: 233px; height: 251px;
    background: var(--white); z-index: 3; display: flex; align-items: center; justify-content: center;
    text-align: center; color: var(--black); font-weight: 500; font-size: 25px; line-height: 34px;
  }

  .copyright { position: absolute; right: 97px; top: 663px; font-size: 11px; color: var(--black); z-index: 3; }
</style>
</head>
<body>
<div class="page">
  <header class="banner">DARE TO DREAM CANADIAN...</header>

  <div class="map-decor" role="img" aria-label="Large red map of Canada behind the content panel"></div>

  <div class="brand">
    <div class="brand-row"><span class="brand-name">ORV</span><span class="brand-dot"></span></div>
    <div class="tagline">Taking you onwards.......</div>
  </div>

  <ul class="nav">
    <li><svg viewBox="0 0 14 14"><path d="M1 5h6V1l6 6-6 6V9H1z" fill="#fff"/></svg>Home</li>
    <li class="active"><svg viewBox="0 0 14 14"><path d="M1 5h6V1l6 6-6 6V9H1z" fill="#fff"/></svg>About Us</li>
    <li><svg viewBox="0 0 14 14"><path d="M1 5h6V1l6 6-6 6V9H1z" fill="#fff"/></svg>Services</li>
    <li><svg viewBox="0 0 14 14"><path d="M1 5h6V1l6 6-6 6V9H1z" fill="#fff"/></svg>Contact Us</li>
    <li><svg viewBox="0 0 14 14"><path d="M1 5h6V1l6 6-6 6V9H1z" fill="#fff"/></svg>ORV Mission</li>
  </ul>

  <div class="member">
    <span class="member-badge" role="img" aria-label="Membership badge"></span>
    <span class="member-name">PLMAT</span>
  </div>

  <div class="social" aria-label="Social links">
    <span></span><span></span><span></span><span></span>
  </div>

  <main class="content">
    <h1 class="content-title">ABOUT US</h1>
    <div class="content-body">
      <p>Delvan Kroth, CEO of Orvane Business Group, has vast knowledge in the field of Student Recruitment &amp; Higher Education. He is an MBA from Canada and is very well known in the India-Canada education corridor since 2004. He has served as India, Africa &amp; Middle East Head for Maplecrest College in the past, in addition to providing consultant services for various elite institutions including, Harwick College, BC, Brenlow College, Ottawa, Prairieview Technical College, Manitoba, and Tidewater College, BC.</p>
      <p class="narrow">Mr. Kroth contributed significantly towards Maplecrest College's immense growth of international students from his region. During his tenure, the college witnessed over <span class="highlight">400% increase</span> in enrolment. This was the highest increase in numbers a medium-sized college in Canada had ever witnessed!</p>
      <p class="narrow">Mr. Kroth is a seasoned and well-respected professional in the Higher Education sector. His key strengths include Student Recruitment, Counseling and Agent Network Development. Delvan has been a mentor in Training, and Team Lead for successfully launching and establishing overseas education services for various Indian businesses focusing on education. New Service Launches, Market Penetration and Development have been areas of focus for him within the industry.</p>
      <div class="portrait">Image of<br>Mr. Kroth<br>Comes Here</div>
    </div>
  </main>

  <footer class="copyright">© 2013 orvanebusinessgroup.com. All rights reserved.</footer>
</div>
</body>
</html>
```